Book Cover for Fitness Trainer for Men

My name is Daisy Mae Corwin. I am a female Fitness Trainer for Men.
I need a new Book Cover Design for my second book and a back of the book.
Both with updated text.
#A… Book Cover… I like the bright red and yellow colors.
I like the weight rack and the bold headline Font
#B… Book Cover…I like the full frontal sexier body. I don not like the font style.
I want the new design sexier; super sexy. Even more eye catching for guys.
I want to push the envelope to the point of almost too much sexy.
An Brindle book 6”x9”, 150 pages

Target Market(s)

Men

Industry/Entity Type

Health and fitness for men

Colors
FFF300
FFF600
FEFA6F
FFFEC7
FFFEE8
EB3D1F
EC4F4E
F09395
F8D3D4
FCEDEE

Requirements
Must have
• Sexy & eye catching.

```html
<!DOCTYPE html>
<html lang="en">
<head>
<meta charset="utf-8">
<title>Helping Guys Get Fit, Fierce, &amp; Firm – Volume II – Book Cover</title>
<link rel="stylesheet" href="https://fonts.googleapis.com/css2?family=Anton&family=Barlow:wght@400;600;700&family=Barlow+Condensed:wght@500;600;700&display=swap">
<style>
  :root{
    --page-bg:#d9d9d9;
    --red-deep:#7e1020;
    --red:#a8162c;
    --red-bright:#c11a30;
    --yellow:#f2c512;
    --gold:#d9921c;
    --white:#ffffff;
    --skin-light:#e9b9a0;
    --skin-mid:#c98a70;
    --spine-line:#f5f5f5;
  }
  *{margin:0;padding:0;box-sizing:border-box}
  html,body{width:960px;height:1200px;overflow:hidden;background:var(--page-bg)}
  .canvas{position:relative;width:960px;height:1200px}
  .spread{position:absolute;left:30px;top:275px;width:900px;height:649px;overflow:hidden;
    box-shadow:0 18px 40px rgba(0,0,0,.25)}

  /* ---------- back cover ---------- */
  .back-cover{position:absolute;left:0;top:0;width:433px;height:649px;
    background:linear-gradient(180deg,var(--red) 0%,var(--red-bright) 45%,var(--red-deep) 100%);color:var(--white);
    font-family:'Barlow',sans-serif}
  .back-topband{position:absolute;left:0;top:0;width:433px;height:47px;
    background:linear-gradient(90deg,#b8501e,var(--gold) 60%,var(--yellow) 100%)}
  .deco-block{position:absolute;background:var(--yellow)}
  .deco-block.one{left:238px;top:0;width:52px;height:47px;background:var(--red-bright)}
  .deco-block.two{left:330px;top:0;width:40px;height:320px;opacity:.55}
  .deco-block.three{left:330px;top:113px;width:103px;height:24px;opacity:.55}
  .trainer-photo{position:absolute;left:0;top:300px;width:190px;height:270px;
    background:radial-gradient(ellipse at 40% 40%,rgba(120,40,40,.7),rgba(120,20,30,0) 70%)}
  .back-text{position:absolute;left:48px;width:340px;font-size:7.3px;line-height:1.45;text-align:center}
  .back-text strong{font-weight:700}
  .intro{top:49px}
  .promise{top:111px;font-size:8px;font-weight:700}
  .community{top:144px}
  .gymrats{top:187px}
  .works-heading{position:absolute;left:86px;top:228px;font-family:'Barlow Condensed',sans-serif;
    font-weight:700;font-size:16px;color:var(--yellow)}
  .testimonials{position:absolute;left:88px;top:252px;width:270px;list-style:none;font-size:7.2px;line-height:1.45}
  .testimonials li{margin-bottom:4px}
  .real-men{position:absolute;left:95px;top:427px;width:210px;text-align:center;font-size:8px;font-weight:700;line-height:1.45}
  .heart-badge{position:absolute}
  .mission{position:absolute;left:66px;top:485px;width:120px;font-family:'Barlow Condensed',sans-serif;
    font-weight:600;font-size:8.6px;line-height:1.4;color:var(--yellow)}
  .portrait{position:absolute;left:192px;top:467px;width:86px;height:86px;border-radius:50%;
    border:3px solid var(--yellow);background:radial-gradient(circle at 50% 40%,var(--skin-light),var(--skin-mid) 70%,#8a5a3e)}
  .signature{position:absolute;left:288px;top:497px}
  .signature .name{font-weight:600;font-size:11px}
  .signature .role{font-size:7.5px;opacity:.9}
  .bottom-band{position:absolute;left:0;top:571px;width:467px;height:31px;background:var(--yellow);
    font-family:'Barlow Condensed',sans-serif;font-weight:700;color:var(--red);font-size:12px;
    display:flex;align-items:center}
  .bottom-band .pitch{margin-left:48px}
  .bottom-band .spine-vol{position:absolute;left:440px;font-family:'Anton',sans-serif;font-size:13px}

  /* ---------- spine ---------- */
  .spine{position:absolute;left:433px;top:0;width:34px;height:649px;background:var(--red)}
  .spine-text{position:absolute;left:17px;transform-origin:0 0;transform:rotate(-90deg);white-space:nowrap;
    display:flex;align-items:center;gap:6px}
  .spine-title{top:314px;margin-left:-12px}
  .spine-title .small{font-family:'Barlow Condensed',sans-serif;font-weight:700;font-size:8px;line-height:.95;color:var(--white)}
  .spine-title .big{font-family:'Anton',sans-serif;font-size:22px;color:var(--white)}
  .spine-role{top:445px;margin-left:-4px;font-family:'Barlow Condensed',sans-serif;font-weight:600;font-size:9px;color:var(--yellow)}
  .spine-author{top:560px;margin-left:-7px;font-family:'Barlow',sans-serif;font-weight:700;font-size:11px;color:var(--white);letter-spacing:.5px}
  .spine-rule{position:absolute;top:-20px;width:1px;height:690px;background:var(--spine-line)}

  /* ---------- front cover ---------- */
  .front-cover{position:absolute;left:467px;top:0;width:433px;height:649px;
    background:linear-gradient(180deg,var(--red-bright),var(--red) 60%,var(--red-deep))}
  .front-yellow{position:absolute;background:var(--yellow)}
  .front-yellow.top{left:200px;top:0;width:233px;height:120px}
  .front-yellow.side{left:360px;top:130px;width:73px;height:230px;opacity:.9}
  .front-yellow.mid{left:0;top:110px;width:433px;height:40px;background:linear-gradient(90deg,rgba(242,197,18,0),var(--yellow) 80%);opacity:.6}
  .model-photo{position:absolute;left:12px;top:0;width:300px;height:649px;
    background:linear-gradient(90deg,rgba(233,185,160,0) 0%,var(--skin-light) 25%,var(--skin-light) 70%,rgba(233,185,160,0) 100%)}
  .author-block{position:absolute;right:38px;top:44px;text-align:right;color:var(--white)}
  .author-block .author{font-family:'Barlow Condensed',sans-serif;font-weight:700;font-size:23px;line-height:1;text-shadow:0 1px 3px rgba(0,0,0,.35)}
  .author-block .role{font-family:'Barlow Condensed',sans-serif;font-weight:700;font-size:14px;line-height:1.2;text-shadow:0 1px 3px rgba(0,0,0,.35)}
  .title{position:absolute;right:34px;top:176px;width:340px;color:var(--white);font-family:'Anton',sans-serif;
    font-weight:400;text-shadow:0 2px 6px rgba(0,0,0,.25)}
  .title .line{display:flex;justify-content:flex-end;align-items:center;height:100px}
  .title .lead{font-family:'Barlow Condensed',sans-serif;font-weight:700;font-size:24px;line-height:.95;text-align:right;margin-right:10px;margin-top:12px}
  .title .word{font-size:90px;line-height:100px;letter-spacing:-1px}
  .title .amp{font-size:40px;line-height:1;margin-right:6px;margin-top:34px}
  .subtitle{position:absolute;right:36px;top:486px;text-align:right;font-family:'Barlow Condensed',sans-serif;
    font-weight:700;font-size:17px;line-height:1.25;color:var(--yellow)}
  .volume{position:absolute;right:38px;top:571px;width:90px;height:31px;background:var(--yellow);
    font-family:'Anton',sans-serif;color:var(--red);font-size:18px;display:flex;align-items:center;justify-content:center}
</style>
</head>
<body>
<div class="canvas">
  <div class="spread">

    <section class="back-cover">
      <div class="back-topband"></div>
      <div class="deco-block one"></div>
      <div class="deco-block two"></div>
      <div class="deco-block three"></div>
      <div class="trainer-photo" role="img" aria-label="Faded photo of a muscular man lifting a dumbbell"></div>

      <p class="back-text intro">I've been using eye candy to get guys interested in health and fitness since the day I walked in the gym and turned heads. I figured if you wanted Tits &amp; Ass I'd give it to you. Enough to make a buck and get my guys healthier. As a personal fitness trainer for Men I've learned…that not all Guys are the same. Each of you is different and You need to find what works for You. When you do … the belly fat burns off, your waist tightens, and your health improves.</p>
      <p class="back-text promise">You'll love the new you. Your girl friend will love it. Your wife will love it.<br>Nothing a woman loves more than a long rock hard man in shape.</p>
      <p class="back-text community">While everybody in the fitness community screams and yells about gym memberships, 30 day challenges, and complete diet changes … My Guys don't do all that. My Guys are Real Men with Real bodies. Real Men that work for a living and don't have time to live in the gym.</p>
      <p class="back-text gymrats">Real men are tired of gym rats with "Look at me" egos, God given 1% body fat and abs you'll never get. These guys are full of Shit! And they're the first one to buy my book. Ya gotta love it.</p>

      <h2 class="works-heading">You need to find what works for you.</h2>

      <svg class="heart-badge" style="left:45px;top:254px" width="30" height="30" viewBox="0 0 30 30" aria-hidden="true">
        <circle cx="15" cy="15" r="13" fill="#d3202f"/><circle cx="15" cy="15" r="13" fill="none" stroke="#8e0f1c" stroke-width="1.5"/>
        <path d="M15 21 L9 15 A3.4 3.4 0 0 1 15 10.5 A3.4 3.4 0 0 1 21 15 Z" fill="#fff"/>
      </svg>
      <ul class="testimonials">
        <li>«I made a few adjustment in my meals added a minimum amount of exercise and lost 17 pounds in three months. Thanks Daisy. Couldn't have done it without you.»</li>
        <li>«<strong>Daisy I took your bait</strong> and it actually made sense. Can't believe you got me exercising. My gut shrunk and had to buy new pants. Best 20 bucks I ever spent.»</li>
        <li>«<strong>I've tried a few expensive</strong> 30day programs but your <strong>Ultimate Workout</strong> was all I ever needed. You're right <strong>No F**king</strong> secret here.»</li>
        <li>«Strategically eating Fast food is genius. Never thought I could still eat "the good stuff" and lose weight. WOW!»</li>
        <li>«<strong>My increasing weight</strong> was scaring the hell out of me. Showing me that it's the little changes I can do…that has changed everything.»</li>
        <li>«<strong>Everybody wanted me to make big</strong> drastic changes in my life. I can't do that. All these little «Tricks of the Trade «I can do.» Thank you Daisy.»</li>
      </ul>
      <svg class="heart-badge" style="left:338px;top:400px" width="62" height="62" viewBox="0 0 62 62" aria-hidden="true">
        <circle cx="31" cy="31" r="28" fill="#d3202f"/><circle cx="31" cy="31" r="28" fill="none" stroke="#8e0f1c" stroke-width="2"/>
        <path d="M31 44 L18 31 A7 7 0 0 1 31 21.5 A7 7 0 0 1 44 31 Z" fill="#fff"/>
      </svg>
      <p class="real-men">Real Men can be fit, healthy and in shape no matter their size, weight, or body fat.</p>

      <p class="mission">My mission is to get your lazy ass in shape by finding what works for you.<br>If I need to get your attention first… Then that's what I'll do.</p>
      <div class="portrait" role="img" aria-label="Round portrait photo of the author"></div>
      <div class="signature">
        <p class="name">Daisy Mae Corwin</p>
        <p class="role">Fitness Trainer for Men</p>
      </div>
    </section>

    <section class="spine">
      <div class="spine-text spine-title">
        <span class="small">Helping<br>Guys Get</span>
        <span class="big">FIT, FIERCE, &amp; FIRM</span>
      </div>
      <div class="spine-text spine-role">Fitness Trainer for Men</div>
      <div class="spine-text spine-author">DAISY MAE CORWIN</div>
    </section>

    <div class="bottom-band">
      <span class="pitch">Think you can do Twenty bucks to Get You Fit, Fierce, and Firm?</span>
      <span class="spine-vol">II</span>
    </div>

    <section class="front-cover">
      <div class="front-yellow top"></div>
      <div class="front-yellow side"></div>
      <div class="front-yellow mid"></div>
      <div class="model-photo" role="img" aria-label="Photo of a woman in a red bikini, torso from chin to thighs"></div>

      <div class="author-block">
        <p class="author">DAISY MAE CORWIN</p>
        <p class="role">Fitness Trainer or Men</p>
      </div>

      <h1 class="title">
        <span class="line"><span class="lead">Helping<br>Guys Get</span><span class="word">FIT,</span></span>
        <span class="line"><span class="word">FIERCE,</span></span>
        <span class="line"><span class="amp">&amp;</span><span class="word">FIRM</span></span>
      </h1>

      <p class="subtitle">so Belly Fat Burns Off,<br>Your Waist Tightens,<br>&amp; You Feel Stronger</p>
      <div class="volume">Volume II</div>
    </section>

    <div class="spine-rule" style="left:433px"></div>
    <div class="spine-rule" style="left:467px"></div>
  </div>
</div>
</body>
</html>
```